Plenko - Shoe Fitting App : Foot scanning app, 3D reconstruction and Fit recommandation.

We are a startup that has developed a 3D scanning App that compares the 3d reconstructed foot to the 3D Last (mould) of a shoe to find the best match and recommend a shoe size with a graphical representation of the fit on a reconstructed foot without texturing. The challenge of this app is to have a simple and intuitive onboarding of the user with clean and crisp ui and a simple tutorial for foot scanning. 3D representation of the fit is also key. What you see is what you feel is what we would like to achieve.

Target Market(s)

Sneaker Brands and athletic shoes brands

Industry/Entity Type

Footwear

Font styles to use
Other font styles liked:
• Oswald or Droid Serif

Colors
0094D4
00A9DD
6FCCEA
C7EBF8
E9F6FB

Requirements
Must have
• Simple intuitive UI to onboard the customer to scan his bare foot (please look at attached image on how to scan the foot). You must flip your phone so that the screen is facing your foot. Start at 40cm distance form the front of your foot and turn 360% slowly to capture the foot while you feel the aptic of the phone. That needs to be presented with a simple animation that the user can easily understand and skip if he is a returning customer and knows how to do that. the rest of the UI is to present the result of the scanned foot for the user to use to get his fit and size. The other must have is the final result screen. Where the user will a representation of the foot (snug, loose ) of different predefined areas of the foot so he can choose the fit that he likes and not necessarily the size that we suggest. Must match website design (https://www.plenko.example)
Nice to have
• An animation of the whole process (scan-compare 3d foot with 3d shoe last(or mould) and get the 3D result of the best fit + associated size. Optionaly, an option to play with your foot and transform it (avatar like with accessories and colours)
Should not have
• Too many colours. Too much text. No gender type. No race type.

```html
<!DOCTYPE html>
<html lang="en">
<head>
<meta charset="utf-8">
<title>Plenko – Scanning Process</title>
<link href="https://fonts.googleapis.com/css2?family=Inter:wght@400;500;600;800;900&family=Noto+Serif:wght@700&display=swap" rel="stylesheet">
<style>
  :root{
    --board:#1c1c1c;
    --screen-light:#ffffff;
    --screen-dark:#000000;
    --ink:#111111;
    --ink-soft:#2a2a2a;
    --button:#f3f3f3;
    --dialog:#2b2b2b;
    --dialog-line:#3c3c3c;
    --accent:#3fb8b2;
    --accent-card:#4ab8b5;
    --indicator-dark:#1e3d36;
    --white:#ffffff;
  }
  *{margin:0;padding:0;box-sizing:border-box}
  html,body{width:1200px;height:495px;overflow:hidden;background:var(--board)}
  .board{position:relative;width:1200px;height:495px;background:var(--board);border-radius:28px;overflow:hidden;font-family:"Inter",sans-serif}
  .board-title{position:absolute;top:68px;left:0;width:100%;text-align:center;color:var(--white);font-weight:900;font-size:74px;letter-spacing:-1.5px;line-height:1}
  .phone{position:absolute;top:185px;width:109px;height:236px;border-radius:8px;overflow:hidden;background:var(--screen-light)}
  .phone.dark{background:var(--screen-dark)}
  .phone.photo{background:radial-gradient(ellipse at 40% 30%,#3a2a22 0%,#231812 55%,#140d09 100%)}
  .status{position:absolute;top:4px;left:0;width:100%;height:8px;display:flex;justify-content:space-between;align-items:center;padding:0 6px 0 9px;font-size:5px;font-weight:600;color:var(--ink)}
  .dark .status,.photo .status{color:var(--white)}
  .status svg{height:4px;width:19px}
  .screen-title{position:absolute;top:18px;width:100%;text-align:center;font-family:"Noto Serif",serif;font-weight:700;font-size:5.2px;color:var(--ink)}
  .app-name{position:absolute;top:19px;width:100%;text-align:center;font-size:3.6px;color:var(--ink-soft)}
  .back{position:absolute;top:18px;left:7px;width:4px;height:6px}
  .art{position:absolute;border-radius:4px}
  .caption{position:absolute;left:6px;right:6px;text-align:center;font-size:4.2px;line-height:6.6px;color:var(--ink)}
  .btn-row{position:absolute;top:209px;left:5px;right:5px;display:flex;gap:5px}
  .btn{flex:1;height:13px;background:var(--button);border-radius:2px;display:flex;align-items:center;justify-content:center;gap:2px;font-size:4.2px;color:var(--ink)}
  .btn svg{width:5px;height:5px}
  .indicator{position:absolute;bottom:6px;left:36px;width:37px;height:1.3px;border-radius:1px;background:var(--indicator-dark)}
  .photo .indicator{background:var(--white)}
  .dialog{position:absolute;top:87px;left:17px;width:75px;height:62px;background:var(--dialog);border-radius:3px;color:var(--white);text-align:center}
  .dialog-title{margin-top:9px;font-size:4.5px;font-weight:500}
  .dialog-body{margin:2px 6px 0;font-size:3.1px;line-height:4.9px;color:#e2e2e2}
  .dialog-action{position:absolute;left:0;width:100%;height:12.5px;border-top:0.5px solid var(--dialog-line);display:flex;align-items:center;justify-content:center;font-size:4.3px;color:var(--accent)}
  .dialog-action.primary{top:37px;font-weight:500}
  .dialog-action.secondary{top:49.5px}
  .scan-card{position:absolute;left:5.5px;top:60px;width:98px;height:126px;background:var(--accent-card);border-radius:4px}
  .scan-frame{position:absolute;left:10px;top:16px;width:78px;height:88px}
  .scan-label{position:absolute;top:108px;width:100%;text-align:center;font-size:4.3px;color:var(--white)}
</style>
</head>
<body>
<main class="board">
  <h1 class="board-title">Scanning Process</h1>

  <!-- Home -->
  <section class="phone" style="left:177px">
    <div class="status"><span>9:41</span><svg viewBox="0 0 38 8"><rect x="0" y="5" width="2" height="3" fill="currentColor"/><rect x="3" y="3.5" width="2" height="4.5" fill="currentColor"/><rect x="6" y="2" width="2" height="6" fill="currentColor"/><rect x="9" y="0.5" width="2" height="7.5" fill="currentColor"/><path d="M14 3a6 6 0 0 1 8 0l-1 1a4.5 4.5 0 0 0-6 0zM16 5a3 3 0 0 1 4 0l-2 2.5z" fill="currentColor"/><rect x="26" y="1" width="10" height="6" rx="1.5" fill="currentColor"/><rect x="36.6" y="3" width="1" height="2" fill="currentColor"/></svg></div>
    <h2 class="screen-title">Home</h2>
    <div class="art" role="img" aria-label="Illustration of hands holding a phone toward a foot, with small sparkles" style="left:10px;top:62px;width:90px;height:80px;background:radial-gradient(ellipse at 35% 50%,#eadfd6 0%,#f6f1ec 45%,#fff 75%)"></div>
    <p class="caption" style="top:175px">Let's get started. Click start to begin scanning</p>
    <div class="btn-row">
      <div class="btn"><svg viewBox="0 0 10 10"><ellipse cx="5" cy="6" rx="2.2" ry="3.6" fill="var(--ink)"/></svg>Left Foot</div>
      <div class="btn"><svg viewBox="0 0 10 10"><ellipse cx="5" cy="6" rx="2.2" ry="3.6" fill="var(--ink)"/></svg>Right Foot</div>
    </div>
    <div class="indicator"></div>
  </section>

  <!-- Right foot intro -->
  <section class="phone" style="left:300px">
    <div class="status"><span>9:41</span><svg viewBox="0 0 38 8"><rect x="0" y="5" width="2" height="3" fill="currentColor"/><rect x="3" y="3.5" width="2" height="4.5" fill="currentColor"/><rect x="6" y="2" width="2" height="6" fill="currentColor"/><rect x="9" y="0.5" width="2" height="7.5" fill="currentColor"/><path d="M14 3a6 6 0 0 1 8 0l-1 1a4.5 4.5 0 0 0-6 0zM16 5a3 3 0 0 1 4 0l-2 2.5z" fill="currentColor"/><rect x="26" y="1" width="10" height="6" rx="1.5" fill="currentColor"/><rect x="36.6" y="3" width="1" height="2" fill="currentColor"/></svg></div>
    <h2 class="screen-title">Right Foot</h2>
    <div class="art" role="img" aria-label="Illustration of a hand holding a phone with its screen facing outward" style="left:24px;top:73px;width:52px;height:70px;background:linear-gradient(160deg,#c9f1ee 0%,#e9f6f4 45%,#fbe2d6 100%)"></div>
    <p class="caption" style="top:175px">Flip your phone to use the front-facing sensors. Tap 'Start' to begin scanning.</p>
    <div class="btn-row"><div class="btn">Start</div></div>
    <div class="indicator"></div>
  </section>

  <!-- Camera start -->
  <section class="phone dark" style="left:423px">
    <div class="status"><span>9:41</span><svg viewBox="0 0 38 8"><rect x="0" y="5" width="2" height="3" fill="currentColor"/><rect x="3" y="3.5" width="2" height="4.5" fill="currentColor"/><rect x="6" y="2" width="2" height="6" fill="currentColor"/><rect x="9" y="0.5" width="2" height="7.5" fill="currentColor"/><path d="M14 3a6 6 0 0 1 8 0l-1 1a4.5 4.5 0 0 0-6 0zM16 5a3 3 0 0 1 4 0l-2 2.5z" fill="currentColor"/><rect x="26" y="1" width="10" height="6" rx="1.5" fill="currentColor"/><rect x="36.6" y="3" width="1" height="2" fill="currentColor"/></svg></div>
  </section>

  <!-- Scan failed -->
  <section class="phone dark" style="left:546px">
    <div class="status"><span>9:41</span><svg viewBox="0 0 38 8"><rect x="0" y="5" width="2" height="3" fill="currentColor"/><rect x="3" y="3.5" width="2" height="4.5" fill="currentColor"/><rect x="6" y="2" width="2" height="6" fill="currentColor"/><rect x="9" y="0.5" width="2" height="7.5" fill="currentColor"/><path d="M14 3a6 6 0 0 1 8 0l-1 1a4.5 4.5 0 0 0-6 0zM16 5a3 3 0 0 1 4 0l-2 2.5z" fill="currentColor"/><rect x="26" y="1" width="10" height="6" rx="1.5" fill="currentColor"/><rect x="36.6" y="3" width="1" height="2" fill="currentColor"/></svg></div>
    <div class="dialog">
      <p class="dialog-title">Scan Failed</p>
      <p class="dialog-body">To ensure a successful scan, please adjust your speed, positioning, or lighting.</p>
      <div class="dialog-action primary">Try Again</div>
      <div class="dialog-action secondary">Go to Tutorial</div>
    </div>
  </section>

  <!-- Processing -->
  <section class="phone photo" style="left:669px" role="img" aria-label="Blurred camera view of the room behind the scan card">
    <div class="status"><span>9:41</span><svg viewBox="0 0 38 8"><rect x="0" y="5" width="2" height="3" fill="currentColor"/><rect x="3" y="3.5" width="2" height="4.5" fill="currentColor"/><rect x="6" y="2" width="2" height="6" fill="currentColor"/><rect x="9" y="0.5" width="2" height="7.5" fill="currentColor"/><path d="M14 3a6 6 0 0 1 8 0l-1 1a4.5 4.5 0 0 0-6 0zM16 5a3 3 0 0 1 4 0l-2 2.5z" fill="currentColor"/><rect x="26" y="1" width="10" height="6" rx="1.5" fill="currentColor"/><rect x="36.6" y="3" width="1" height="2" fill="currentColor"/></svg></div>
    <div class="scan-card">
      <svg class="scan-frame" viewBox="0 0 78 88" fill="none" stroke="#ffffff" stroke-width="0.8">
        <path d="M0 7V0h7M71 0h7v7M78 81v7h-7M7 88H0v-7"/>
      </svg>
      <div class="art" role="img" aria-label="Wireframe point cloud of a scanned foot" style="left:18px;top:24px;width:62px;height:72px;background:radial-gradient(ellipse at 55% 50%,#8fdcd8 0%,#6ccbc7 45%,rgba(74,184,181,0) 75%)"></div>
      <p class="scan-label">Processing...</p>
    </div>
    <div class="indicator"></div>
  </section>

  <!-- Reconstruction failed -->
  <section class="phone photo" style="left:792px" role="img" aria-label="Dimmed camera view behind the error dialog">
    <div class="status"><span>9:41</span><svg viewBox="0 0 38 8"><rect x="0" y="5" width="2" height="3" fill="currentColor"/><rect x="3" y="3.5" width="2" height="4.5" fill="currentColor"/><rect x="6" y="2" width="2" height="6" fill="currentColor"/><rect x="9" y="0.5" width="2" height="7.5" fill="currentColor"/><path d="M14 3a6 6 0 0 1 8 0l-1 1a4.5 4.5 0 0 0-6 0zM16 5a3 3 0 0 1 4 0l-2 2.5z" fill="currentColor"/><rect x="26" y="1" width="10" height="6" rx="1.5" fill="currentColor"/><rect x="36.6" y="3" width="1" height="2" fill="currentColor"/></svg></div>
    <div class="dialog">
      <p class="dialog-title">Reconstruction Failed</p>
      <p class="dialog-body">We couldn't complete the reconstruction. Please check your scan quality and try again</p>
      <div class="dialog-action primary">Retry Scan</div>
      <div class="dialog-action secondary">Go to Tutorial</div>
    </div>
    <div class="indicator"></div>
  </section>

  <!-- Result check -->
  <section class="phone" style="left:915px">
    <div class="status"><span>9:41</span><svg viewBox="0 0 38 8"><rect x="0" y="5" width="2" height="3" fill="currentColor"/><rect x="3" y="3.5" width="2" height="4.5" fill="currentColor"/><rect x="6" y="2" width="2" height="6" fill="currentColor"/><rect x="9" y="0.5" width="2" height="7.5" fill="currentColor"/><path d="M14 3a6 6 0 0 1 8 0l-1 1a4.5 4.5 0 0 0-6 0zM16 5a3 3 0 0 1 4 0l-2 2.5z" fill="currentColor"/><rect x="26" y="1" width="10" height="6" rx="1.5" fill="currentColor"/><rect x="36.6" y="3" width="1" height="2" fill="currentColor"/></svg></div>
    <svg class="back" viewBox="0 0 4 6" fill="none" stroke="var(--ink)" stroke-width="0.7"><path d="M3.5 0.5L1 3l2.5 2.5"/></svg>
    <p class="app-name">Stridely</p>
    <div class="art" role="img" aria-label="3D reconstruction of the scanned foot" style="left:20px;top:63px;width:66px;height:72px;background:radial-gradient(ellipse at 55% 55%,#9c6a55 0%,#b8836c 40%,rgba(255,255,255,0) 72%)"></div>
    <p class="caption" style="top:180px">Please check that the reconstruction of your foot seems correct</p>
    <div class="btn-row">
      <div class="btn"><svg viewBox="0 0 10 10" fill="none" stroke="var(--ink)" stroke-width="0.8"><path d="M1 3V1h2M7 1h2v2M9 7v2H7M3 9H1V7"/></svg>Scan again</div>
      <div class="btn"><svg viewBox="0 0 10 10"><path d="M1 7l2-4 2 2 4 1v2H1z" fill="var(--ink)"/></svg>My Fit</div>
    </div>
    <div class="indicator"></div>
  </section>
</main>
</body>
</html>
```